Satchel & Sundial needs new business card design

I need a new business card design. I'm looking for out-of-the-box design which represents the freedom of being a location independent entrepreneur.
I offer coaching, retreats and trips.
I would like to see designs with and without the photo.
Colors I use are black (#000000), green (#25A796) and brown (#D7C38C)
Website satchelandsundial.example

Target Market(s)

location independent entrepreneurs, digital nomads, people looking to swap the 9 to 5 for a lifestyle business

Industry/Entity Type

Business

Contact Information for Business Card

Dorota Falkner
Your Lifestyle Business Coach, Retreat & Trip Leader
http://satchelandsundial.example
hello@satchelandsundial.example
Live a life you don't need a holiday from

Font styles to use
Serif
Sans Serif

Requirements
Must have
• One side should contain only the logo. I would also consider having the "Live a life you don't need a holiday from" on that side too (depending on how it looks)
• Please show both sides on the designs.

```html
<!DOCTYPE html>
<html lang="en">
<head>
<meta charset="utf-8">
<title>Satchel &amp; Sundial – Business Card</title>
<link rel="stylesheet" href="https://fonts.googleapis.com/css2?family=Oswald:wght@300;400;500;600&family=Kaushan+Script&display=swap">
<style>
  :root {
    --ink: #111111;
    --green: #1f9a8a;
    --card: #fbfbfb;
    --backdrop: #dcdcdc;
    --edge: #cfcfcf;
  }
  * { box-sizing: border-box; margin: 0; padding: 0; }
  html, body { width: 1200px; height: 576px; overflow: hidden; }
  body {
    background: var(--backdrop);
    position: relative;
    font-family: "Oswald", sans-serif;
    color: var(--ink);
  }
  .card {
    position: absolute;
    top: 138px;
    width: 484px;
    height: 294px;
    background: var(--card);
    border: 1px solid var(--edge);
    border-radius: 8px;
  }
  .card--front { left: 81px; }
  .card--back { left: 602px; }

  .wordmark {
    font-family: "Oswald", sans-serif;
    font-weight: 400;
    text-transform: uppercase;
    color: var(--ink);
    letter-spacing: 0.01em;
    white-space: nowrap;
    line-height: 1;
  }
  .card--front .wordmark {
    position: absolute;
    left: 0; right: 0;
    top: 126px;
    text-align: center;
    font-size: 38px;
  }
  .card--back .wordmark {
    position: absolute;
    right: 24px;
    top: 34px;
    font-size: 28px;
  }

  .holder { position: absolute; left: 26px; top: 148px; }
  .holder__name {
    font-weight: 600;
    font-size: 18px;
    text-transform: uppercase;
    letter-spacing: 0.01em;
    line-height: 1.1;
  }
  .holder__role {
    margin-top: 6px;
    font-weight: 400;
    font-size: 11px;
    color: var(--green);
  }

  .contact { position: absolute; left: 26px; top: 210px; list-style: none; }
  .contact__item {
    display: flex;
    align-items: center;
    height: 20px;
    font-size: 11.5px;
    font-weight: 400;
  }
  .contact__icon { width: 12px; height: 12px; margin-right: 11px; flex: none; }
  .contact__social-mark {
    width: 9px; height: 9px; margin-right: 8px; flex: none;
    background: var(--ink); border-radius: 2px;
  }
  .contact__handle { color: var(--green); }
  .accent { color: var(--green); }

  .motto {
    position: absolute;
    right: 22px;
    top: 252px;
    font-family: "Kaushan Script", cursive;
    font-size: 12.5px;
    color: var(--green);
    white-space: nowrap;
  }
</style>
</head>
<body>

  <section class="card card--front" aria-label="Card front">
    <div class="wordmark">Satchel &amp; Sundial</div>
  </section>

  <section class="card card--back" aria-label="Card back">
    <div class="wordmark">Satchel &amp; Sundial</div>

    <div class="holder">
      <h1 class="holder__name">Dorota Falkner</h1>
      <p class="holder__role">Your Lifestyle Business Coach, Retreat &amp; Trip Leader</p>
    </div>

    <ul class="contact">
      <li class="contact__item">
        <svg class="contact__icon" viewBox="0 0 12 12" aria-hidden="true">
          <rect x="0.5" y="2" width="11" height="8" fill="var(--green)"/>
          <path d="M0.8 2.4 L6 6.6 L11.2 2.4" fill="none" stroke="var(--card)" stroke-width="1"/>
        </svg>
        hello@satchelandsundial.example
      </li>
      <li class="contact__item">
        <svg class="contact__icon" viewBox="0 0 12 12" aria-hidden="true">
          <circle cx="6" cy="6" r="5.3" fill="none" stroke="var(--green)" stroke-width="1.2"/>
          <ellipse cx="6" cy="6" rx="2.3" ry="5.3" fill="none" stroke="var(--green)" stroke-width="1"/>
          <line x1="0.7" y1="6" x2="11.3" y2="6" stroke="var(--green)" stroke-width="1"/>
        </svg>
        www.<span class="accent">satchelandsundial</span>.example
      </li>
      <li class="contact__item">
        <span class="contact__social-mark" aria-hidden="true"></span>
        <span class="contact__handle">/satchelandsundial</span>
      </li>
    </ul>

    <p class="motto">Live a life you dont need a holiday from</p>
  </section>

</body>
</html>
```